Marlowe Group needs a business card

I would like the card to be simple but modern and elegant.
I like black and white.
or black and gold.
we are a private finance lender and also are involved in property and property developments.

please look at the business card photos i provided i would like M.G only one one side and all the other details on the other side use fonts that tie in with my theme.

Industry/Entity Type

Finance

Contact Information for Business Card

Marlowe Group (M.G) Daniel Marlowe M: 0413586207 E: danmarl@inboxmail.test

Font styles to use
Other font styles liked:
• Use fonts that would reflect our business

Colors
000000
ffffff

Requirements
Must have
• one side of details
• other side has either M.G or Marlowe Group like in the photos provided

```html
<!DOCTYPE html>
<html lang="en">
<head>
<meta charset="utf-8">
<title>Marlowe Group — Business Card</title>
<link rel="stylesheet" href="https://fonts.googleapis.com/css2?family=Encode+Sans+Semi+Condensed:wght@500&family=Hind:wght@300;400&display=swap">
<style>
  :root {
    --backdrop: #d9d9d9;
    --card-light: #ffffff;
    --card-dark: #000000;
    --ink: #3f3f3f;
    --ink-strong: #111111;
    --ink-inverse: #ffffff;
    --shadow: rgba(0, 0, 0, 0.28);
  }
  * { margin: 0; padding: 0; box-sizing: border-box; }
  html, body {
    width: 1200px;
    height: 900px;
    overflow: hidden;
    background: var(--backdrop);
  }
  .stage {
    position: relative;
    width: 1200px;
    height: 900px;
  }
  .card {
    position: absolute;
    top: 257px;
    width: 397px;
    height: 397px;
    border-radius: 24px;
    box-shadow: 3px 4px 8px var(--shadow);
  }
  .card--details { left: 205px; background: var(--card-light); }
  .card--brand {
    left: 653px;
    background: var(--card-dark);
    display: flex;
    align-items: center;
    justify-content: center;
  }
  .brand-name {
    font-family: "Encode Sans Semi Condensed", "Arial Narrow", sans-serif;
    font-weight: 500;
    line-height: 1.05;
    letter-spacing: -0.5px;
  }
  .card--details .brand-name {
    position: absolute;
    left: 28px;
    top: 48px;
    font-size: 62px;
    color: var(--ink-strong);
  }
  .card--brand .brand-name {
    font-size: 50px;
    color: var(--ink-inverse);
    text-align: center;
  }
  .person-name {
    position: absolute;
    left: 24px;
    top: 247px;
    font-family: "Hind", Arial, sans-serif;
    font-weight: 300;
    font-size: 29px;
    letter-spacing: 0.5px;
    color: var(--ink);
  }
  .contact-list {
    position: absolute;
    left: 26px;
    top: 306px;
    list-style: none;
    font-family: "Hind", Arial, sans-serif;
    font-weight: 400;
    font-size: 21px;
    color: var(--ink-strong);
  }
  .contact-item {
    display: flex;
    align-items: center;
    gap: 7px;
    height: 28px;
  }
  .contact-icon { width: 14px; flex: none; }
</style>
</head>
<body>
<main class="stage">
  <section class="card card--details" aria-label="Card front with contact details">
    <div class="brand-name">Marlowe<br>Group</div>
    <div class="person-name">Daniel Marlowe</div>
    <ul class="contact-list">
      <li class="contact-item">
        <svg class="contact-icon" viewBox="0 0 14 20" height="18" aria-hidden="true">
          <rect x="2" y="1" width="10" height="18" rx="2" fill="none" stroke="#111" stroke-width="1.8"/>
          <circle cx="7" cy="15.5" r="1.1" fill="#111"/>
        </svg>
        <span>0413586207</span>
      </li>
      <li class="contact-item">
        <svg class="contact-icon" viewBox="0 0 14 10" height="10" aria-hidden="true">
          <rect x="0" y="0" width="14" height="10" fill="#111"/>
          <path d="M0.5 0.8 L7 5.8 L13.5 0.8" fill="none" stroke="#fff" stroke-width="1.2"/>
        </svg>
        <span>danmarl@inboxmail.test</span>
      </li>
    </ul>
  </section>

  <section class="card card--brand" aria-label="Card back with company name">
    <div class="brand-name">Marlowe<br>Group</div>
  </section>
</main>
</body>
</html>
```